New bussiness card, using company logo.
Lionel Brisk
Manager/Director
Brisk Property Developments
Po Box 5347
Ferngate Central
Nth
0491 638 205
lionel@briskpropertydevelopments
eye catching, vibrant colours, professional

```html
<!DOCTYPE html>
<html lang="en">
<head>
<meta charset="utf-8">
<title>Brisk Property Developments – Business Card</title>
<link rel="stylesheet" href="https://fonts.googleapis.com/css2?family=Arimo:wght@400;700&family=Roboto+Condensed:wght@400;700&display=swap">
<style>
  :root {
    --stage: #d6d6d6;
    --red-light: #c41e32;
    --red-mid: #9e1426;
    --red-dark: #5e0b16;
    --white: #ffffff;
    --leaf: #6cc04a;
    --grass-light: #6fae3a;
    --grass-dark: #2f6b1c;
    --ink-red: #d3202f;
  }
  * { box-sizing: border-box; margin: 0; padding: 0; }
  html, body { width: 1200px; height: 818px; overflow: hidden; }
  body {
    background: var(--stage);
    display: flex;
    align-items: center;
    justify-content: center;
    gap: 60px;
    font-family: "Arimo", Arial, sans-serif;
  }
  .card {
    position: relative;
    width: 525px;
    height: 300px;
    overflow: hidden;
    box-shadow: 0 6px 18px rgba(0,0,0,0.25);
  }

  /* Front */
  .front__brand {
    position: absolute; left: 0; top: 0;
    width: 330px; height: 150px;
    background: var(--white);
    display: flex; align-items: center; justify-content: center; gap: 12px;
  }
  .brand-mark {
    width: 22px; height: 22px;
    background: var(--leaf);
    flex: none;
  }
  .brand-name {
    font-family: "Arimo", Arial, sans-serif;
    font-weight: 700;
    font-size: 22px;
    line-height: 1.1;
    color: var(--ink-red);
    text-transform: uppercase;
  }
  .front__identity {
    position: absolute; left: 0; top: 150px;
    width: 330px; height: 150px;
    background: linear-gradient(160deg, var(--red-light) 0%, var(--red-mid) 55%, var(--red-dark) 100%);
    border-top: 4px solid var(--leaf);
    padding: 40px 0 0 70px;
    color: var(--white);
    font-family: "Roboto Condensed", "Arial Narrow", sans-serif;
  }
  .person-name { font-weight: 700; font-size: 30px; }
  .person-role { font-weight: 400; font-size: 24px; margin-top: 4px; }
  .lawn {
    position: absolute;
    background: radial-gradient(ellipse at 60% 40%, var(--grass-light) 0%, var(--grass-dark) 100%);
  }
  .front__lawn { right: 0; top: 0; width: 195px; height: 300px; }

  /* Back */
  .back {
    background: linear-gradient(120deg, var(--red-dark) 0%, var(--red-mid) 35%, var(--red-light) 60%, var(--red-mid) 100%);
  }
  .back__stripes { position: absolute; inset: 0; }
  .back__details {
    position: absolute; left: 36px; top: 50px;
    color: var(--white);
    font-size: 17px;
    line-height: 1.45;
  }
  .back__details .company { margin-bottom: 14px; }
</style>
</head>
<body>

  <section class="card front" aria-label="Business card front">
    <div class="front__brand">
      <span class="brand-mark"></span>
      <span class="brand-name">Brisk Property<br>Developments</span>
    </div>
    <div class="front__identity">
      <p class="person-name">Lionel Brisk</p>
      <p class="person-role">Manager/Director</p>
    </div>
    <div class="lawn front__lawn" role="img" aria-label="Close-up photograph of a green lawn"></div>
  </section>

  <section class="card back" aria-label="Business card back">
    <svg class="back__stripes" width="525" height="300" viewBox="0 0 525 300">
      <polygon points="300,300 525,110 525,300" fill="var(--grass-dark)" role="img" aria-label="Green lawn photograph"/>
      <polygon points="280,300 525,94 525,110 300,300" fill="var(--white)"/>
      <polygon points="262,300 525,78 525,94 280,300" fill="var(--leaf)"/>
    </svg>
    <div class="back__details">
      <p class="company">Brisk Property Developments</p>
      <p>Po Box 5347</p>
      <p>Ferngate Central Nth</p>
      <p>0491 638 205</p>
      <p>lionel@briskpropertydevelopments.com</p>
    </div>
  </section>

</body>
</html>
```